A wine Label for a new brand of New Zealand Wine

We are looking for a Wine Label for our "Harbor Pine" brand of wines from North Otago New Zealand. We would like the label to perhaps use the HP as a logo and the rest up to the designer. We have our vineyards located in the Waitaki Valley New Zealand which is a southern region with mountains and a river flowing past our vineyard. Photos attached of Dramatic Landscape. Also attached is a basic outline of requirements for the front bottle of the label. The rear bottle label will contain writing about the wines background plus statutory regulations on Alc. Vol, bar code etc. Front Label size to be no Larger than 80mm deep by 100 mm wide. The label can be simple or graphic, whatever the designer chooses.
Target Market(s)
New Wine Brand
Look and feel
Each slider illustrates characteristics of the customer's brand and the style your logo design should communicate.

```html
<!DOCTYPE html>
<html lang="en">
<head>
<meta charset="utf-8">
<title>Harbor Pine – Pinot Gris 2015 Front Label</title>
<link rel="stylesheet" href="https://fonts.googleapis.com/css2?family=Cinzel:wght@400;600&family=Raleway:wght@500&display=swap">
<style>
  :root {
    --canvas: #ffffff;
    --gold-light: #d9c04a;
    --gold-mid: #b59a2a;
    --gold-deep: #7d6a16;
    --label-dark: #221f14;
    --band-brown: #4a3c0c;
    --ink-cream: #f4efe0;
    --name-gold: #c9ad3a;
  }
  html, body {
    margin: 0;
    padding: 0;
    width: 1200px;
    height: 1000px;
    overflow: hidden;
    background: var(--canvas);
  }
  .canvas {
    position: relative;
    width: 1200px;
    height: 1000px;
  }
  .wine-label {
    position: absolute;
    left: 332px;
    top: 164px;
    width: 536px;
    height: 672px;
    background: linear-gradient(135deg, var(--gold-mid) 0%, var(--gold-light) 25%, var(--gold-deep) 55%, var(--gold-light) 80%, var(--gold-mid) 100%);
  }
  .label-art {
    position: absolute;
    inset: 0;
  }
  .brand-name {
    position: absolute;
    left: 0;
    width: 100%;
    top: 170px;
    margin: 0;
    text-align: center;
    font-family: "Cinzel", serif;
    font-weight: 600;
    font-size: 74px;
    line-height: 76px;
    color: var(--name-gold);
    letter-spacing: 1px;
  }
  .varietal {
    position: absolute;
    left: 0;
    width: 100%;
    top: 398px;
    text-align: center;
    font-family: "Cinzel", serif;
    color: var(--ink-cream);
  }
  .varietal .grape {
    display: block;
    font-size: 30px;
    line-height: 36px;
  }
  .varietal .vintage {
    display: block;
    font-size: 28px;
    line-height: 38px;
  }
  .region {
    position: absolute;
    left: 0;
    width: 100%;
    top: 518px;
    text-align: center;
    font-family: "Cinzel", serif;
    font-size: 19px;
    color: var(--ink-cream);
  }
  .origin {
    position: absolute;
    left: 0;
    width: 100%;
    top: 558px;
    text-align: center;
    font-family: "Raleway", sans-serif;
    font-weight: 500;
    font-size: 16px;
    letter-spacing: 3px;
    color: var(--ink-cream);
  }
</style>
</head>
<body>
<main class="canvas">
  <section class="wine-label" aria-label="Harbor Pine Pinot Gris front label">
    <svg class="label-art" viewBox="0 0 536 672" width="536" height="672" aria-hidden="true">
      <defs>
        <linearGradient id="rimGold" x1="0" y1="0" x2="1" y2="1">
          <stop offset="0" stop-color="#f0d85a"/>
          <stop offset="0.5" stop-color="#9a8019"/>
          <stop offset="1" stop-color="#e6cb4c"/>
        </linearGradient>
        <linearGradient id="bandBrown" x1="0" y1="0" x2="1" y2="0">
          <stop offset="0" stop-color="#2c2710"/>
          <stop offset="0.5" stop-color="#5a4a0e"/>
          <stop offset="1" stop-color="#2c2710"/>
        </linearGradient>
      </defs>
      <!-- label shield -->
      <path class="shield-rim" d="M54,112 Q54,80 92,70 Q268,22 444,70 Q482,80 482,112 V566 Q482,598 444,608 Q268,656 92,608 Q54,598 54,566 Z" fill="url(#rimGold)"/>
      <path class="shield-body" d="M66,116 Q66,90 98,82 Q268,36 438,82 Q470,90 470,116 V562 Q470,588 438,596 Q268,642 98,596 Q66,588 66,562 Z" fill="var(--label-dark)"/>
      <!-- brand panel frame with crest notch -->
      <path class="brand-frame" d="M86,127 H208 V100 Q268,52 328,100 V127 H450 V342 H86 Z" fill="none" stroke="url(#rimGold)" stroke-width="6"/>
      <circle class="crest-circle" cx="268" cy="120" r="34" fill="none" stroke="url(#rimGold)" stroke-width="5"/>
      <!-- varietal band -->
      <rect class="varietal-band" x="66" y="382" width="404" height="108" fill="url(#bandBrown)"/>
      <rect x="66" y="382" width="404" height="2" fill="#6b5a18"/>
      <rect x="66" y="488" width="404" height="2" fill="#6b5a18"/>
    </svg>

    <h1 class="brand-name">Harbor<br>Pine</h1>

    <p class="varietal">
      <span class="grape">Pinot Gris</span>
      <span class="vintage">2015</span>
    </p>

    <p class="region" style="margin:0">Waitaki Valley - North Ortago</p>
    <p class="origin" style="margin:0">NEW ZEALAND WINE</p>
  </section>
</main>
</body>
</html>
```